Website Design for a Project Management Consulting Business

I have a logo design already and now I need a website.
I am a project manager and run my own consulting business.
Currently I am under contract with 3 major Vantage 400 companies. I'd like a website I can direct current and future clients.
My job is running IT projects and working with developers to deliver business priorities.
The website should be professional and clean - I work IT projects and would like to incorporate that into any theme.
I'd like the site to have several page or breakoff links - sections would include : about me, about my services, a page to display all of my certification badges, another page to talk about highlights from past projects and so on.
Looking for a collaborative experience.

Industry/Entity Type

Vantage 400 Consulting Firm - Project Management

Coding

Coded - Design and coding required

Number of Pages Required

1 page

Font styles to use
Serif

Colors
0094D4
00A9DD
6FCCEA
C7EBF8
E9F6FB
EE7325
F08F49
F5BC92
FAE3D3
FDF4ED

Requirements
Must have
• Sections that are a must: About Me (bio), About My Services, About my Certifications and Credentials, Experience on Past Projects,
Nice to have
• I have added the logo below - I'd like to use the logo and have it prominent ; should be professional and inviting

```html
<!DOCTYPE html>
<html lang="en">
<head>
<meta charset="utf-8">
<title>Meridian Delivery Partners — Project Management Consulting</title>
<link href="https://fonts.googleapis.com/css2?family=Barlow:wght@400;500;600;700&family=Barlow+Semi+Condensed:wght@600;700&display=swap" rel="stylesheet">
<style>
:root{
  --navy:#0b3558;
  --blue:#0094D4;
  --blue-2:#00A9DD;
  --blue-3:#6FCCEA;
  --blue-4:#C7EBF8;
  --blue-5:#E9F6FB;
  --orange:#EE7325;
  --orange-2:#F08F49;
  --orange-3:#F5BC92;
  --peach:#FAE3D3;
  --peach-2:#FDF4ED;
  --text:#2c3440;
  --white:#ffffff;
}
*{box-sizing:border-box;margin:0;padding:0}
html,body{width:1200px;height:3600px;overflow:hidden}
body{position:relative;background:var(--white);font-family:"Barlow",sans-serif;color:var(--text)}
.abs{position:absolute}
.head{font-family:"Barlow Semi Condensed",sans-serif;font-weight:700;color:var(--navy);text-transform:uppercase;line-height:1}
.head .accent{color:var(--blue-2)}
.dash{display:inline-block;width:44px;height:2px;background:var(--orange);margin-left:18px;vertical-align:middle;position:relative;top:12px}
.btn{position:absolute;display:flex;align-items:center;justify-content:center;border-radius:24px;background:linear-gradient(90deg,var(--orange),var(--orange-2));color:var(--white);font-family:"Barlow Semi Condensed",sans-serif;font-weight:700;font-size:16px;letter-spacing:1.2px;text-transform:uppercase}
.rule-group{position:absolute;display:flex;gap:7px}
.rule-group span{width:2px;height:100%;background:var(--orange-3)}
.photo{position:absolute}

/* header */
.brand{left:22px;top:26px;display:flex;align-items:center;gap:12px}
.brand-mark{width:44px;height:44px;background:var(--blue)}
.brand-name{font-family:"Barlow",sans-serif;font-weight:600;font-size:30px;color:var(--navy);letter-spacing:1px}
.topline{right:24px;top:18px;display:flex;gap:32px;font-family:"Barlow Semi Condensed",sans-serif;font-weight:600;font-size:15px;color:var(--navy)}
.topline span{display:flex;align-items:center;gap:8px}
.nav{right:24px;top:54px;display:flex;gap:16px;font-size:13px;font-weight:500;color:var(--navy);letter-spacing:.6px}
.nav a{color:inherit;text-decoration:none;display:flex;align-items:center;gap:8px}
.nav a::before{content:"";width:16px;height:1.5px;background:var(--blue)}

/* hero */
.hero-title{left:158px;top:222px;font-size:42px}
.hero-title .big{display:block;font-size:54px;margin-top:8px;color:var(--blue-2)}
.hero-copy{left:158px;top:330px;width:370px;font-size:18px;line-height:27px}

/* services */
.section-title{font-size:46px;text-align:center;width:100%}
.service{position:absolute;width:280px;height:104px;border:2px solid var(--blue-2);border-radius:4px;background:var(--white);display:flex;align-items:center;justify-content:center;text-align:center;font-weight:700;font-size:18px;line-height:26px;color:var(--navy);text-transform:uppercase}

/* about */
.about-copy{left:636px;top:1178px;width:406px;font-size:15px;line-height:24px}
.about-copy p+p{margin-top:24px}
.stat{position:absolute;top:1462px}
.stat b{display:block;font-family:"Barlow Semi Condensed",sans-serif;font-size:32px;color:var(--orange);line-height:1}
.stat span{font-family:"Barlow Semi Condensed",sans-serif;font-weight:600;font-size:17px;color:var(--navy)}

/* certs */
.badge{position:absolute;width:80px;height:80px}
.badge .halo{position:absolute;left:22px;top:22px;width:66px;height:66px;border-radius:50%;background:var(--blue-4)}
.badge .mark{position:absolute;inset:0;border-radius:50%}

/* trusted */
.quote{left:180px;top:2187px;width:380px;font-size:15.5px;line-height:24px}
.quote-mark{left:156px;top:2172px;font-family:"Barlow",sans-serif;font-weight:700;font-size:90px;line-height:1;color:var(--blue-3)}
.cite{left:180px;top:2320px;font-size:15px;line-height:24px}
.cite b{display:block;color:var(--navy);font-weight:700;text-transform:uppercase}

/* experience */
.exp-card{position:absolute;top:2591px;width:270px}
.exp-card .frame{width:270px;height:204px;border:7px solid var(--blue-4);background:var(--white)}
.exp-card .frame div{width:100%;height:100%}
.exp-card h3{margin-top:30px;font-family:"Barlow Semi Condensed",sans-serif;font-weight:700;font-size:23px;line-height:29px;color:var(--navy);text-align:center;text-transform:uppercase}

/* contact */
.contact-copy{left:158px;top:3070px;width:340px;font-size:15.5px;line-height:24px}
.contact-row{position:absolute;left:158px;display:flex;gap:10px;font-size:17px;color:var(--navy)}
.contact-row .ico{width:26px;height:26px;flex:none}
.contact-row .lbl{width:82px;font-family:"Barlow Semi Condensed",sans-serif;font-weight:600}
.contact-row .val{font-family:"Barlow Semi Condensed",sans-serif;font-weight:600;line-height:24px}
.field{position:absolute;height:37px;border:1.5px solid var(--navy);border-radius:5px;padding:10px 14px;font-family:"Barlow Semi Condensed",sans-serif;font-size:13px;color:#6a7a88;text-transform:uppercase;background:var(--white)}

/* footer */
.foot-head{font-family:"Barlow Semi Condensed",sans-serif;font-weight:700;font-size:20px;color:var(--navy);text-transform:uppercase}
.foot-list{list-style:none;font-size:12.5px;line-height:24px;color:var(--navy)}
.social{left:815px;top:3504px;display:flex;gap:16px}
.social span{width:18px;height:18px;border-radius:50%;background:var(--blue)}
.copyright{left:722px;top:3542px;font-size:13px;color:var(--navy)}
</style>
</head>
<body>

<!-- background shapes -->
<svg class="abs" style="left:0;top:0" width="1200" height="3600" aria-hidden="true">
  <path d="M180 0 H1200 V520 C1080 560 980 540 880 520 C700 480 400 520 260 300 C200 200 180 90 180 0Z" fill="#E9F6FB"/>
  <circle cx="1198" cy="232" r="112" fill="#C7EBF8"/>
  <path d="M0 570 C120 580 250 680 300 800 C340 900 240 950 0 970Z" fill="#E9F6FB"/>
  <circle cx="1150" cy="933" r="72" fill="#FAE3D3"/>
  <path d="M0 3000 C300 2920 600 2920 900 2970 C1050 2995 1150 2990 1200 2960 V3120 C1000 3100 600 3130 0 3120Z" fill="#FDF4ED" opacity=".0"/>
  <path d="M1200 2930 C1120 2960 1090 3000 1120 3060 C1150 3110 1200 3120 1200 3120Z" fill="#E9F6FB"/>
  <path d="M0 3380 C200 3350 420 3400 640 3380 C860 3360 1050 3330 1200 3360 V3600 H0Z" fill="#E9F6FB"/>
  <path d="M360 2680 C360 2560 440 2476 600 2476 C760 2476 838 2560 838 2680 V2830 C838 2890 760 2912 600 2912 C440 2912 360 2890 360 2830Z" fill="#FDF4ED"/>
</svg>

<!-- header -->
<div class="abs brand"><span class="brand-mark"></span><span class="brand-name">MERIDIAN DELIVERY</span></div>
<div class="abs topline">
  <span><svg width="16" height="16" viewBox="0 0 24 24" fill="none" stroke="#EE7325" stroke-width="2"><path d="M5 3h4l2 5-3 2a12 12 0 006 6l2-3 5 2v4a2 2 0 01-2 2A18 18 0 013 5a2 2 0 012-2z"/></svg>Call Me - (555) 010-2040</span>
  <span><svg width="16" height="14" viewBox="0 0 24 20" fill="none" stroke="#EE7325" stroke-width="2"><rect x="1" y="1" width="22" height="18" rx="2"/><path d="M1 3l11 8 11-8"/></svg>Emai Me - hello@meridiandelivery.com</span>
</div>
<nav class="abs nav"><a>ABOUT ME</a><a>MY SERVICES</a><a>CERTIFICATIONS AND CREDENTIALS</a><a>EXPERIENCE</a><a>CONTACT</a></nav>

<!-- hero -->
<div class="rule-group" style="left:74px;top:186px;height:300px"><span></span><span></span><span></span></div>
<h1 class="abs head hero-title">Extensive Experienced<span class="big">Consultant</span></h1>
<p class="abs hero-copy">Serves as Principal Lead Consultant on waterfall and agile contract opportunities.</p>
<div class="btn" style="left:158px;top:408px;width:184px;height:42px">My Experience</div>
<div class="photo" role="img" aria-label="Portrait of the consultant in a pinstripe suit" style="left:570px;top:100px;width:471px;height:473px;border-radius:62% 38% 40% 60% / 48% 40% 60% 52%;background:linear-gradient(150deg,#2a2f36,#4b4f57 60%,#6b6e74)"></div>
<svg class="abs" style="left:580px;top:447px" width="126" height="126" aria-hidden="true"><circle cx="63" cy="63" r="63" fill="#F08F49"/></svg>

<!-- services -->
<h2 class="abs head section-title" style="top:656px">About <span class="accent">My Services</span><span class="dash"></span></h2>
<div class="service" style="left:158px;top:752px">Leading Scaled Agile<br>Scrum Teams</div>
<div class="service" style="left:460px;top:752px">Leading Scaled Agile<br>Scrum Teams</div>
<div class="service" style="left:761px;top:752px">Leading Scaled Agile<br>Scrum Teams</div>
<div class="service" style="left:158px;top:879px">Leading Scaled Agile<br>Scrum Teams</div>
<div class="service" style="left:460px;top:879px">Leading Scaled Agile<br>Scrum Teams</div>
<div class="service" style="left:761px;top:879px">Leading Scaled Agile<br>Scrum Teams</div>

<!-- about me -->
<svg class="abs" style="left:156px;top:1073px" width="470" height="566" aria-hidden="true"><path d="M200 0 C330 0 470 120 470 300 C470 470 380 566 230 566 C80 566 0 470 0 320 C0 140 80 0 200 0Z" fill="#FDF4ED"/></svg>
<svg class="abs" style="left:494px;top:1090px" width="108" height="108" aria-hidden="true"><circle cx="54" cy="54" r="54" fill="#FAE3D3"/></svg>
<div class="photo" role="img" aria-label="Full portrait of the consultant in a blue plaid blazer" style="left:190px;top:1088px;width:400px;height:548px;border-radius:48% 48% 10% 10% / 30% 30% 6% 6%;background:linear-gradient(180deg,#6f8fb3,#5478a3 55%,#3f5f88)"></div>
<h2 class="abs head" style="left:636px;top:1116px;font-size:46px">About <span class="accent">Me</span><span class="dash"></span></h2>
<div class="abs about-copy">
  <p>Marcus Ellery is the Owner of Meridian Delivery Partners, LLC and serves as Principal Lead Consultant on waterfall and agile contract opportunities.</p>
  <p>Meridian Delivery Partners, LLC has engaged on a contract basis with Vantage 400 companies across various industries including banking and credit unions, global supply chain, and international food distribution. Marcus Ellery brings 12 years of experience to his clients encompassing various project methodologies including: waterfall, agile, and hybrid frameworks.</p>
</div>
<div class="stat" style="left:636px"><b>500+</b><span>Satisfied Clients</span></div>
<div class="stat" style="left:808px"><b>99%</b><span>Success of Works</span></div>
<div class="btn" style="left:631px;top:1552px;width:153px;height:41px">Know More</div>

<!-- certifications -->
<h2 class="abs head section-title" style="top:1724px">Certifications <span class="accent">&amp; Credentials</span><span class="dash"></span></h2>
<svg class="abs" style="left:158px;top:1843px" width="22" height="44" aria-hidden="true"><path d="M18 2L4 22l14 20" fill="none" stroke="#EE7325" stroke-width="3"/></svg>
<svg class="abs" style="left:1020px;top:1843px" width="22" height="44" aria-hidden="true"><path d="M4 2l14 20L4 42" fill="none" stroke="#EE7325" stroke-width="3"/></svg>
<div class="badge" style="left:210px;top:1825px" role="img" aria-label="Certification badge"><div class="halo"></div><div class="mark" style="background:#fff;border:5px solid #4b2a82"></div></div>
<div class="badge" style="left:348px;top:1825px" role="img" aria-label="Certification badge"><div class="halo"></div><div class="mark" style="background:#fff;border:5px solid #4b2a82"></div></div>
<div class="badge" style="left:485px;top:1825px" role="img" aria-label="Certification badge"><div class="halo"></div><div class="mark" style="border-radius:8px;transform:rotate(45deg) scale(.78);background:#1f4e79"></div></div>
<div class="badge" style="left:623px;top:1825px" role="img" aria-label="Certification badge"><div class="halo"></div><div class="mark" style="border-radius:8px;transform:rotate(45deg) scale(.78);background:#1f4e79"></div></div>
<div class="badge" style="left:762px;top:1825px" role="img" aria-label="Certification badge"><div class="halo"></div><div class="mark" style="background:#e8582b"></div></div>
<div class="badge" style="left:900px;top:1825px" role="img" aria-label="Certification badge"><div class="halo"></div><div class="mark" style="background:#f2a81d"></div></div>

<!-- trusted -->
<div class="rule-group" style="left:74px;top:2005px;height:405px"><span></span><span></span><span></span></div>
<h2 class="abs head" style="left:158px;top:2046px;font-size:46px;line-height:58px">Trusted by Biggest<br><span class="accent">Business Names</span><span class="dash"></span></h2>
<div class="abs quote-mark" aria-hidden="true">&ldquo;</div>
<p class="abs quote">Lorem ipsum dolor sit amet, consectetur adipiscing elit, sed do eiusmod tempor incididunt ut labore et dolore magna aliqua. Ut enim ad minim veniam, quis nostrud exercitation ullamco laboris nisi ut aliquip ex ea commodo consequat.</p>
<div class="abs cite"><b>Dana Whitfield</b>Northwind Labs</div>
<svg class="abs" style="left:887px;top:2242px" width="154" height="154" aria-hidden="true"><circle cx="77" cy="77" r="77" fill="#C7EBF8"/></svg>
<div class="photo" role="img" aria-label="Photo of the consultant at the office in front of a monitor" style="left:630px;top:2000px;width:411px;height:414px;border-radius:40% 60% 45% 55% / 30% 40% 60% 70%;background:linear-gradient(160deg,#d9d4cf,#a7a19c 45%,#3d3f47)"></div>
<svg class="abs" style="left:601px;top:2005px" width="126" height="126" aria-hidden="true"><circle cx="63" cy="63" r="63" fill="#F08F49"/></svg>

<!-- experience -->
<h2 class="abs head section-title" style="top:2500px;color:var(--blue-2)">Experience<span class="dash"></span></h2>
<div class="exp-card" style="left:158px"><div class="frame"><div role="img" aria-label="Portrait photo" style="background:linear-gradient(160deg,#8a7a6a,#4a3e36)"></div></div><h3>Senior Scaled Scrum<br>Master</h3></div>
<div class="exp-card" style="left:465px"><div class="frame"><div role="img" aria-label="Portrait photo" style="background:linear-gradient(180deg,#eef1f4,#9fb0c5)"></div></div><h3>Senior Project<br>Manger</h3></div>
<div class="exp-card" style="left:773px"><div class="frame"><div role="img" aria-label="Portrait photo" style="background:linear-gradient(160deg,#1e2024,#4a4d55)"></div></div><h3>Senior Program<br>Manger</h3></div>

<!-- contact -->
<div class="rule-group" style="left:74px;top:2987px;height:321px"><span></span><span></span><span></span></div>
<h2 class="abs head" style="left:158px;top:3004px;font-size:46px">Get <span class="accent">In Touch</span><span class="dash"></span></h2>
<p class="abs contact-copy">We're glad to discuss your organisation's situation. So please contact us via the details below, or enter your request.</p>
<div class="contact-row" style="top:3164px">
  <svg class="ico" viewBox="0 0 26 26" fill="none" stroke="#00A9DD" stroke-width="1.6"><circle cx="13" cy="13" r="12"/><path d="M13 20s-5-5-5-8.5a5 5 0 0110 0C18 15 13 20 13 20z"/><circle cx="13" cy="11.5" r="1.8"/></svg>
  <span class="lbl">Address -</span><span class="val">88 Harbor Line Rd,<br>NY, 10001, USA.</span></div>
<div class="contact-row" style="top:3222px">
  <svg class="ico" viewBox="0 0 26 26" fill="none" stroke="#00A9DD" stroke-width="1.6"><circle cx="13" cy="13" r="12"/><path d="M9 7h2.5l1 3-1.6 1.2a7 7 0 003.4 3.4L15.5 13l3 1v2.5A1.5 1.5 0 0117 18 10 10 0 017.5 8.5 1.5 1.5 0 019 7z"/></svg>
  <span class="lbl">Call Me -</span><span class="val" style="font-weight:700">(555) 010-2040</span></div>
<div class="contact-row" style="top:3256px">
  <svg class="ico" viewBox="0 0 26 26" fill="none" stroke="#00A9DD" stroke-width="1.6"><circle cx="13" cy="13" r="12"/><rect x="7" y="9" width="12" height="9" rx="1"/><path d="M7 10l6 4 6-4"/></svg>
  <span class="lbl">Emai Me -</span><span class="val" style="text-decoration:underline">hello@meridiandelivery.com</span></div>
<div class="field" style="left:538px;top:3012px;width:240px">First Name</div>
<div class="field" style="left:799px;top:3012px;width:240px">Last Name</div>
<div class="field" style="left:538px;top:3068px;width:240px">Email Address</div>
<div class="field" style="left:799px;top:3068px;width:240px">Phone</div>
<div class="field" style="left:538px;top:3124px;width:240px">Website</div>
<div class="field" style="left:799px;top:3124px;width:240px">Services</div>
<div class="field" style="left:538px;top:3178px;width:501px;height:103px">Message</div>
<div class="btn" style="left:856px;top:3300px;width:182px;height:42px">Send Request</div>

<!-- footer -->
<h4 class="abs foot-head" style="left:158px;top:3416px">Usefull Links</h4>
<ul class="abs foot-list" style="left:158px;top:3454px;width:140px"><li>- About Me</li><li>- Experience</li><li style="line-height:16px;padding:4px 0">- Certifications and<br>&nbsp;&nbsp;Credentials</li><li>- Contact Us</li></ul>
<ul class="abs foot-list" style="left:309px;top:3454px"><li>- Privacy Policy</li><li>- Terms &amp; Conditions</li></ul>
<h4 class="abs foot-head" style="left:481px;top:3416px">Services</h4>
<ul class="abs foot-list" style="left:481px;top:3454px"><li>- Services1</li><li>- Services1</li><li>- Services1</li><li>- Services1</li></ul>
<div class="abs brand" style="left:730px;top:3428px"><span class="brand-mark"></span><span class="brand-name">MERIDIAN DELIVERY</span></div>
<div class="abs social" aria-label="Social profiles"><span></span><span></span><span></span><span></span></div>
<p class="abs copyright">Copyright © 2022 MERIDIAN DELIVERY. All rights reserved.</p>

</body>
</html>
```